Machining Business Order Thank You Insert

I am looking for a business style card to include with orders that I ship. The card needs to thank the recipient for their order, and encourage them to leave a review. The card should include my business name and contact information and have an area to hand write a message.

I mainly sale on Craftlane and my own website. We are a machining an manufacturing business that are in the sale of mostly metal machined and 3d printed plastic products.

The front of the card should include the following:
Logo: (attached)
Snapgram: https://www.snapgram.example/kelvomill/
Friendsbook: https://www.friendsbook.example/KelvoMill
Website: https://www.kelvomill.example/

The back of the card needs an area to write a message

Industry/Entity Type

3D Printing, Machining, Craftlane

Contact Information for Business Card

Black or white front, white back to write a personal message

Font styles to use
Sans Serif

Colors

Designer to choose colors to be used in the design.

Requirements
Must have
• Encourage a review, social media info

```html
<!DOCTYPE html>
<html lang="en">
<head>
<meta charset="utf-8">
<title>KelvoMill – Order Thank You Card</title>
<link href="https://fonts.googleapis.com/css2?family=Barlow:wght@400;500&family=Roboto:wght@400&display=swap" rel="stylesheet">
<style>
  :root {
    --backdrop: #2e2e2e;
    --card-light: #252525;
    --card-dark: #000000;
    --frame-silver: #b9b9b9;
    --accent-orange: #f05a28;
    --text-grey: #8a8a8a;
    --text-light: #c8c8c8;
    --paper: #ffffff;
    --ink: #2a2a2a;
    --ink-soft: #6a6a6a;
    --rule: #cfcfcf;
  }
  * { margin: 0; padding: 0; box-sizing: border-box; }
  html, body {
    width: 1125px; height: 1200px; overflow: hidden;
    background: var(--backdrop);
  }
  .canvas { position: relative; width: 1125px; height: 1200px; }
  .card {
    position: absolute; left: 172px; width: 824px; height: 472px;
    box-shadow: 0 4px 10px rgba(0,0,0,.5);
  }
  .card--front {
    top: 106px;
    background: linear-gradient(90deg, var(--card-light) 0%, #151515 50%, var(--card-dark) 72%);
  }
  .card--back { top: 640px; background: var(--paper); }
  .card__frame {
    position: absolute; inset: 13px 16px 13px 13px;
    border: 3px solid var(--frame-silver);
  }
  .brand-mark {
    position: absolute; left: 50%; transform: translateX(-50%); display: block;
  }
  .card--front .brand-mark { top: 110px; width: 110px; height: 110px; border: 6px solid var(--accent-orange); }
  .wordmark {
    position: absolute; left: 0; right: 0; text-align: center;
    font-family: "Barlow", sans-serif; font-weight: 500; text-transform: uppercase;
  }
  .card--front .wordmark { top: 276px; font-size: 33px; letter-spacing: 9px; color: var(--text-grey); }
  .thanks {
    position: absolute; left: 0; right: 0; text-align: center;
    font-family: "Barlow", sans-serif; font-weight: 400;
  }
  .thanks__title { top: 352px; font-size: 20px; letter-spacing: 3px; text-transform: uppercase; color: var(--text-light); }
  .thanks__review { top: 386px; font-size: 16px; letter-spacing: 1px; color: var(--text-grey); }

  .card--back .card__frame { border-color: var(--rule); }
  .back__header {
    position: absolute; top: 44px; left: 0; right: 0;
    display: flex; justify-content: center; align-items: center; gap: 14px;
  }
  .back__mark { width: 22px; height: 22px; border: 3px solid var(--ink); }
  .back__name {
    font-family: "Barlow", sans-serif; font-weight: 500; font-size: 20px;
    letter-spacing: 6px; text-transform: uppercase; color: var(--ink);
  }
  .message-area {
    position: absolute; top: 110px; left: 70px; right: 70px; height: 210px;
  }
  .message-area__label {
    font-family: "Barlow", sans-serif; font-size: 14px; letter-spacing: 2px;
    text-transform: uppercase; color: var(--ink-soft);
  }
  .message-area__line { height: 44px; border-bottom: 1px solid var(--rule); }
  .contact {
    position: absolute; top: 360px; left: 0; right: 0;
    display: flex; justify-content: center;
    font-family: "Roboto", sans-serif; font-size: 17px; line-height: 24px; color: var(--ink-soft);
  }
  .contact__location { text-align: right; padding-right: 16px; border-right: 1px solid var(--rule); }
  .contact__social { padding-left: 16px; list-style: none; }
  .contact__social li { display: flex; align-items: center; gap: 8px; }
  .social-dot { width: 12px; height: 12px; border-radius: 50%; background: var(--ink-soft); }
</style>
</head>
<body>
<div class="canvas">
  <section class="card card--front">
    <div class="card__frame"></div>
    <span class="brand-mark"></span>
    <h1 class="wordmark">KelvoMill</h1>
    <p class="thanks thanks__title">Thank you for your order</p>
    <p class="thanks thanks__review">Enjoying it? Please leave us a review on Craftlane</p>
  </section>

  <section class="card card--back">
    <div class="card__frame"></div>
    <div class="back__header">
      <span class="back__mark"></span>
      <h2 class="back__name">KelvoMill</h2>
    </div>
    <div class="message-area">
      <p class="message-area__label">A note for you</p>
      <div class="message-area__line"></div>
      <div class="message-area__line"></div>
      <div class="message-area__line"></div>
      <div class="message-area__line"></div>
    </div>
    <div class="contact">
      <div class="contact__location">
        <p>Oakridge Falls, IN</p>
        <p>www.kelvomill.example</p>
      </div>
      <ul class="contact__social">
        <li><span class="social-dot"></span>@kelvomill.example</li>
        <li><span class="social-dot"></span>/kelvomill.example</li>
      </ul>
    </div>
  </section>
</div>
</body>
</html>
```